Corporate Business Card

Very professional, Modern, Not to busy, include phone address email, website
(253) 617-4930, 18761 52nd Avenue S, Kent, WA 98047, martin@plumlinegroup.com, varkoworks.com

Target Market(s)

Manufacturing

Industry/Entity Type

Aero, machining, manufacturing, Off road racing

Contact Information for Business Card

Phone, address email, website

```html
<!DOCTYPE html>
<html lang="en">
<head>
<meta charset="utf-8">
<title>Varko Works – Business Card</title>
<link rel="stylesheet" href="https://fonts.googleapis.com/css2?family=Montserrat:wght@400;500;700;800&display=swap">
<style>
  :root {
    --navy: #17356f;
    --red: #d1232a;
    --ink: #222428;
    --paper: #ffffff;
    --backdrop: #3b3b3b;
  }
  * { margin: 0; padding: 0; box-sizing: border-box; }
  html, body {
    width: 1200px; height: 1059px; overflow: hidden;
    background: var(--backdrop);
    font-family: "Montserrat", Arial, sans-serif;
  }
  .card {
    position: absolute;
    left: 256px;
    width: 688px;
    height: 392px;
    overflow: hidden;
  }
  .card--front { top: 100px; background: var(--paper); }
  .card--back { top: 537px; background: var(--navy); }

  .brand {
    position: absolute;
    display: flex; align-items: center; gap: 12px;
    font-weight: 800;
    letter-spacing: 1px;
    white-space: nowrap;
  }
  .brand__mark { width: 16px; height: 16px; background: var(--red); }
  .card--front .brand { right: 36px; top: 70px; font-size: 40px; color: var(--navy); }
  .card--back .brand {
    left: 0; right: 0; top: 168px; justify-content: center;
    font-size: 52px; color: var(--paper);
  }

  .name-accent {
    position: absolute; left: 0; top: 205px;
    width: 14px; height: 43px; background: var(--red);
  }
  .person__name {
    position: absolute; left: 33px; top: 200px;
    font-size: 27px; font-weight: 700; color: var(--navy);
  }
  .person__role {
    position: absolute; left: 33px; top: 232px;
    font-size: 15px; font-weight: 400; color: var(--ink);
  }
  .person__rule {
    position: absolute; left: 105px; top: 241px;
    width: 442px; height: 1.5px; background: var(--navy);
  }

  .contact {
    position: absolute; left: 32px; top: 281px;
    list-style: none; font-size: 15px; color: var(--ink);
  }
  .contact li { display: flex; align-items: center; gap: 5px; height: 22px; }
  .contact svg { width: 13px; height: 13px; fill: var(--red); flex: none; }

  .address {
    position: absolute; right: 36px; top: 305px;
    font-style: normal; text-align: right;
    font-size: 15px; line-height: 20px; color: var(--ink);
  }

  .footer-band { position: absolute; left: 0; bottom: 0; width: 688px; height: 18px; }
</style>
</head>
<body>

<section class="card card--front">
  <div class="brand"><span class="brand__mark"></span>VARKO WORKS</div>

  <div class="name-accent"></div>
  <h1 class="person__name">Daren Holt</h1>
  <p class="person__role">Founder</p>
  <div class="person__rule"></div>

  <ul class="contact">
    <li>
      <svg viewBox="0 0 16 16" aria-hidden="true"><path d="M1 6c0-2 3-3 7-3s7 1 7 3v1.5h-3.5V6h-7v1.5H1zM4 8h8l2 6H2z"/></svg>
      (253) 617-4930
    </li>
    <li>
      <svg viewBox="0 0 16 16" aria-hidden="true"><path d="M1 3h14v1.2L8 9 1 4.2zM1 6l7 4.7L15 6v7H1z"/></svg>
      martin@plumlinegroup.com
    </li>
    <li>
      <svg viewBox="0 0 16 16" aria-hidden="true"><path d="M8 1a7 7 0 1 0 0 14A7 7 0 0 0 8 1zm-2 3 3 1-1 2 2 1v3l-2 2-1-3-2-1V6z"/></svg>
      www.varkoworks.com
    </li>
  </ul>

  <address class="address">
    18761 52nd Avenue S,<br>
    Kent, WA 98047
  </address>

  <svg class="footer-band" viewBox="0 0 688 18" aria-hidden="true">
    <polygon points="0,0 349,0 329,18 0,18" fill="var(--navy)"/>
    <polygon points="360,0 688,0 688,18 337,18" fill="var(--red)"/>
  </svg>
</section>

<section class="card card--back">
  <div class="brand"><span class="brand__mark"></span>VARKO WORKS</div>
</section>

</body>
</html>
```